Modern Business Card

Modern professional business card with more than just logo and demographic info. Something memorable.

We are a trendy/modern chiropractic group with an emphasis on neurology, hence the minimalist-type brain logo. We want to convey that modern and technical aspect with professionalism and the elite nature of our practice environment.

```html
<!DOCTYPE html>
<html lang="en">
<head>
<meta charset="utf-8">
<title>Cortex Motion Chiropractic – Business Card</title>
<link href="https://fonts.googleapis.com/css2?family=Crimson+Pro:wght@400;500&family=Arimo:wght@400&display=swap" rel="stylesheet">
<style>
  :root {
    --page-bg: #e9e7e6;
    --card-light-top: #f7f4f4;
    --card-light-bottom: #ece6e6;
    --emboss-light: rgba(255,255,255,0.85);
    --emboss-shade: rgba(214,204,204,0.55);
    --card-dark: #050607;
    --accent-blue: #4a7fd0;
    --ink-dark: #2b2b2e;
    --ink-light: #ffffff;
  }
  * { box-sizing: border-box; margin: 0; padding: 0; }
  html, body {
    width: 1200px;
    height: 900px;
    overflow: hidden;
    background: var(--page-bg);
  }
  .canvas {
    position: relative;
    width: 1200px;
    height: 900px;
  }
  .business-card {
    position: absolute;
    left: 120px;
    top: 152px;
    width: 960px;
    height: 596px;
    display: flex;
    box-shadow: 0 18px 40px rgba(0,0,0,0.18);
  }
  .brand-side {
    position: relative;
    width: 502px;
    height: 100%;
    background: linear-gradient(180deg, var(--card-light-top), var(--card-light-bottom));
    border-left: 6px solid var(--accent-blue);
    border-right: 7px solid var(--accent-blue);
    display: flex;
    align-items: center;
    justify-content: center;
    overflow: hidden;
  }
  .emboss-texture {
    position: absolute;
    left: 0;
    top: 20px;
    width: 100%;
    height: 540px;
    background:
      radial-gradient(ellipse 60% 50% at 50% 50%, var(--emboss-light), transparent 70%),
      linear-gradient(90deg, transparent, var(--emboss-shade) 30%, var(--emboss-shade) 70%, transparent);
    opacity: 0.7;
  }
  .brand-name {
    position: relative;
    display: flex;
    align-items: center;
    gap: 16px;
    font-family: "Crimson Pro", serif;
    font-weight: 500;
    color: var(--ink-dark);
    font-size: 42px;
    letter-spacing: 1px;
    text-transform: uppercase;
    line-height: 1.05;
  }
  .brand-mark {
    width: 22px;
    height: 22px;
    border-radius: 50%;
    background: var(--accent-blue);
    flex-shrink: 0;
  }
  .contact-side {
    flex: 1;
    background: var(--card-dark);
    color: var(--ink-light);
    padding: 128px 0 0 46px;
    font-family: "Arimo", Arial, sans-serif;
  }
  .person-name {
    font-family: "Crimson Pro", serif;
    font-weight: 400;
    font-size: 38px;
    letter-spacing: 1px;
    text-transform: uppercase;
    line-height: 1;
  }
  .person-role {
    font-size: 27px;
    margin-top: 10px;
  }
  .address {
    font-size: 27px;
    line-height: 1.33;
    margin-top: 46px;
    font-style: normal;
  }
  .contact-list {
    list-style: none;
    margin-top: 34px;
    font-size: 27px;
    line-height: 1.33;
  }
  .contact-list li {
    display: flex;
    align-items: center;
    gap: 8px;
  }
  .contact-icon {
    width: 27px;
    height: 27px;
    flex-shrink: 0;
  }
</style>
</head>
<body>
<main class="canvas">
  <section class="business-card" aria-label="Business card">
    <div class="brand-side">
      <div class="emboss-texture" role="img" aria-label="Faint embossed pattern of vertical rounded lines behind the practice name"></div>
      <div class="brand-name">
        <span class="brand-mark"></span>
        <span>Cortex Motion<br>Chiropractic</span>
      </div>
    </div>
    <div class="contact-side">
      <h1 class="person-name">Daniel Reyes</h1>
      <p class="person-role">Managing Director</p>
      <address class="address">58 Larkspur Avenue<br>Northvale, 20817</address>
      <ul class="contact-list">
        <li>
          <svg class="contact-icon" viewBox="0 0 24 24" aria-hidden="true">
            <rect x="2" y="2" width="20" height="20" rx="4" fill="none" stroke="#fff" stroke-width="2"/>
            <path d="M8 6c-1 1-1 3 1 6s4 5 6 5c1 0 2-1 2-1l-2-2-2 1c-1-1-3-3-3-4l1-2-2-3z" fill="#fff"/>
          </svg>
          <span>021-555 730 418</span>
        </li>
        <li>
          <svg class="contact-icon" viewBox="0 0 24 24" aria-hidden="true">
            <rect x="2" y="6" width="20" height="13" fill="#fff"/>
            <path d="M2 6l10 8 10-8" fill="none" stroke="#050607" stroke-width="2"/>
          </svg>
          <span>hello@cortexmotion.net</span>
        </li>
        <li>
          <svg class="contact-icon" viewBox="0 0 24 24" aria-hidden="true">
            <g fill="none" stroke="#fff" stroke-width="2">
              <circle cx="12" cy="12" r="10"/>
              <ellipse cx="12" cy="12" rx="4.5" ry="10"/>
              <path d="M2 12h20M4 7h16M4 17h16"/>
            </g>
          </svg>
          <span>www.cortexmotion.net</span>
        </li>
      </ul>
    </div>
  </section>
</main>
</body>
</html>
```